Store Front Window Design

We have a beautiful corner store front dental practice with no window signage. Crazy I know...that's why we need your help.

The final design will be done in all vinyl unless unless you suggest a different medium (meaning we are open to some design idea like using frosted glass, etc...).

The windows provide a lot of natural light so the design needs to keep a lot of natural light coming into the office. Keep in mind vinyl is not opaque so keep the signage aesthetically pleasing and a minimalist design to allow as much natural light in as possible. The design should follow the aesthetic from our logo. or tie into at least. We want a cohesive brand aesthetic.

I submitted some general layout ideas. There is a blue banner with advertising words which we want to be used in the final version. Even though the lettering is black, in reality the letters will be a white vinyl on the outside of the window. When you submit your work, be sure to add any special instructions (aka tell me the vision for the letters is white not black, maybe gold leaf, or forested glass...stuff like that). AND YOU DO NOT HAVE TO FOLLOW MY PATTERN! YOU ARE ARTISTS AND WE ARE LOOKING FOR AN ARTISTIC EYE CATCHING PRESENTATION OF THIS INFORMATION. MAKE IT FLASHY AND ADD SOME AESTHETIC FROM THE TOOTH LOGO.

The store front is 6 windows roughly 60'' x 36'' The smaller windows below are 27'' x 36''. Around the corner there are 3 windows. they are 60'' x 27'' lower windows are 27" x 27". We would like to keep the bottom windows clear and keep the signage on the top windows, however, we are flexible.

The front 6 windows need to have this information worked into the design.

Practice name: Varden and Pellosi Dental & Orthodontics.
Phone numbers: Rosalind Varden DDS: 415.555.0187
Oskar Pellosi DDS:415.555.0243

Expertise: Dr. Varden General Dentistry & Orthodontics
Dr. Pellosi Oral Surgery & Sedation

Address: 1938 Birchwood Ave

A banner across the bottom of the top windows with some key advertisement words: "Clearmold" "Braces" "Implants" "Whiting" "Call today" "Free Consultation" "Oral Surgery" "Sedation". We like the two color idea. Its up to you to decide on the color combo. I used a Dark and light blue, but maybe a Blue and grey would nice to tire in the logo colors?

I have made some mock ideas to get the ball rolling but you do not have to stick to these designs at all, just as long as all the required information is there. Be creative with the layouts, fonts, color scheme, (just remember these are going on windows not necessarily a white background), and graphics/artistic flare (refer to logo for layout inspiration and use the logo as an actual graphic). We are running a miltimillion dollar dental practice so we want these windows to be eye catching to pull in patients and look like a million dollar design. Also all 6 windows dont need ot be used. I am really looking for creative design marketing.

The corner 3 windows need the following information: name, expertise, phone number, banner.

Dr. Varden, General Dentistry & Orthodontics, 415.555.0187
Dr. Pellosi, Oral Surgery & Sedation, 415.555.0243

There is also a front door that needs to be designed. The door is 60'' x 36'' (standard door size) We want simple white vinyl on the outside of the door. We need you to organize the information on the door, pick a easy to read font, maybe use the logo and use some of the front window signage aesthetic? Its up to you...but we we were initially thinking of just making the litters white and keep it simple but again you are the designers.

Practice name: Varden and Pellosi General Dentistry & Orthodontics

Address: 1938 Birchwood Ave

Phone numbers: Dr. Varden 415.555.0187
Dr. Pellosi 415.555.0243

Hours of operation: Mon: call for an appointment
Tues-Thurs: 9am-5pm
Sat: call for an appointment
Sun: Closed

A line saying we speak Spanish: Se Habla Espanol

*****************************************************************************************************
here are some design that we liked and some rough sketches I made to start the ball rolling. Keep in mind that there are 9 windows for the front because its a corner office, but not all of them have to have stuff on it. We want simple, streamline, classy high commanding price point aesthetic. I am hiring you for your artistic minds.

Target Market(s)

anyone who has dental needs

Industry/Entity Type

Dental

Font styles to use
Serif
Sans Serif

Colors

Designer to choose colors to be used in the design.

Requirements
Must have
• 1. The required information (see project description)
• 2. Logo
• 3. Advertisement banner running along the bottom of all 9 windows (6 in front and 3 on the side)
• NOTE: Look at pictures of the store to get a sense of the customers point of view and also as a reference to how your design will be broken up across several windows or maybe you design something special for every window. But we want the banner to run along all the windows to lead customs to the door on the side. Finally the letters will be done in white vinyl unless state otherwise, remember the window needs to let in natural light so the entire window can not be covered in vinyl.
Nice to have
• artistic flare yet simple and sleep and expensive looking aesthetic. work logo into the design.
Should not have
• The goal is to catch someone eye and give them important information about the practice.
• It should not just be words.
• It should not have to many words
• It must be readable font for cards driving by.

```html
<!DOCTYPE html>
<html lang="en">
<head>
<meta charset="utf-8">
<title>Oskar Pellosi D.D.S. – Window Panel</title>
<link href="https://fonts.googleapis.com/css2?family=Montserrat:wght@500;700&family=Oswald:wght@600&display=swap" rel="stylesheet">
<style>
  :root {
    --page-bg: #f2f2f2;
    --panel-bg: #ffffff;
    --teal-dark: #1b6378;
    --teal-light: #4a97a3;
    --banner: #4a97a2;
    --banner-base: #1b6174;
    --art-a: #bfe6f3;
    --art-b: #d7eef0;
    --ink: #111111;
  }
  html, body {
    margin: 0;
    padding: 0;
    width: 1200px;
    height: 1200px;
    overflow: hidden;
    background: var(--page-bg);
  }
  .canvas {
    position: relative;
    width: 1200px;
    height: 1200px;
    background: var(--page-bg);
  }
  .panel {
    position: absolute;
    left: 237px;
    top: 0;
    width: 721px;
    height: 1200px;
    background: var(--panel-bg);
    overflow: hidden;
  }
  .mascot-art {
    position: absolute;
    left: 195px;
    top: 56px;
    width: 324px;
    height: 216px;
    border-radius: 24px;
    background: linear-gradient(135deg, var(--art-b), var(--art-a));
  }
  .doctor-name {
    position: absolute;
    left: 0;
    width: 100%;
    top: 305px;
    margin: 0;
    text-align: center;
    font-family: "Montserrat", sans-serif;
    font-weight: 700;
    font-size: 60px;
    line-height: 74px;
    color: var(--teal-dark);
    letter-spacing: 0.5px;
  }
  .double-rule {
    position: absolute;
    left: 81px;
    width: 556px;
    height: 2px;
    border-top: 2px solid var(--teal-light);
    border-bottom: 2px solid var(--teal-light);
  }
  .rule-top { top: 483px; }
  .rule-bottom { top: 741px; }
  .specialty {
    position: absolute;
    left: 0;
    width: 100%;
    top: 528px;
    margin: 0;
    text-align: center;
    font-family: "Montserrat", sans-serif;
    font-weight: 500;
    font-size: 50px;
    line-height: 56px;
    color: var(--teal-light);
  }
  .phone {
    position: absolute;
    left: 0;
    width: 100%;
    top: 780px;
    text-align: center;
    font-family: "Montserrat", sans-serif;
    font-weight: 700;
    color: var(--teal-dark);
  }
  .phone-area {
    display: flex;
    align-items: center;
    justify-content: center;
    gap: 18px;
    font-size: 92px;
    line-height: 104px;
  }
  .phone-icon { width: 72px; height: 72px; }
  .phone-number {
    font-size: 92px;
    line-height: 100px;
    letter-spacing: 6px;
  }
  .promo-banner {
    position: absolute;
    left: 0;
    top: 1014px;
    width: 100%;
    height: 158px;
    background: var(--banner);
    display: flex;
    align-items: center;
    justify-content: center;
  }
  .promo-banner span {
    font-family: "Oswald", sans-serif;
    font-weight: 600;
    font-size: 68px;
    letter-spacing: 9px;
    color: #ffffff;
  }
  .banner-base {
    position: absolute;
    left: 0;
    top: 1172px;
    width: 100%;
    height: 28px;
    background: var(--banner-base);
  }
</style>
</head>
<body>
<div class="canvas">
  <section class="panel">
    <div class="mascot-art" role="img" aria-label="Hand-drawn illustration of two smiling cartoon kids, one in a nurse cap, one carrying a large light blue tooth"></div>

    <h1 class="doctor-name">OSKAR PELLOSI<br>D.D.S.</h1>

    <div class="double-rule rule-top"></div>
    <p class="specialty">Oral Surgery<br>&amp;<br>Sedation</p>
    <div class="double-rule rule-bottom"></div>

    <div class="phone">
      <div class="phone-area">
        <svg class="phone-icon" viewBox="0 0 72 72" aria-hidden="true">
          <circle cx="36" cy="36" r="33" fill="none" stroke="var(--ink)" stroke-width="3"/>
          <path d="M40 16 l8 4 -5 10 -6 -2 c-3 5 -3 11 0 16 l6 -2 5 10 -8 4 c-10 -8 -10 -32 0 -40z" fill="var(--ink)"/>
        </svg>
        <span>(415)</span>
      </div>
      <div class="phone-number">555-0243</div>
    </div>

    <div class="promo-banner"><span>FREE CONSOLATION</span></div>
    <div class="banner-base"></div>
  </section>
</div>
</body>
</html>
```